Business card design for Brivo Engineering Tandem

We need a new business card design along with all the necessary to place an order. The company is Brivo Engineering Tandem and we recently updated our logo.

```html
<!DOCTYPE html>
<html lang="en">
<head>
<meta charset="utf-8">
<title>Brivo Engineering Tandem – Business Card</title>
<link rel="stylesheet" href="https://fonts.googleapis.com/css2?family=Montserrat:wght@400;500;600;700&display=swap">
<style>
  :root {
    --page-bg: #ece9e4;
    --card-dark: #000000;
    --card-light: #ffffff;
    --brand-grey: #8c8c8c;
    --text-grey: #55575a;
    --accent: #e3bb1f;
    --card-radius: 30px;
  }
  * { margin: 0; padding: 0; box-sizing: border-box; }
  html, body {
    width: 1189px; height: 1200px; overflow: hidden;
    background: var(--page-bg);
    font-family: "Montserrat", Arial, sans-serif;
  }
  .card {
    position: absolute;
    left: 169px;
    width: 851px;
    height: 485px;
    border-radius: var(--card-radius);
    overflow: hidden;
  }
  .card--front { top: 112px; background: var(--card-dark); }
  .card--back  { top: 641px; background: var(--card-light); }

  .brand {
    position: absolute;
    display: flex;
    align-items: center;
    gap: 14px;
  }
  .brand__mark {
    width: 18px; height: 18px;
    background: var(--accent);
    flex: none;
  }
  .brand__name {
    color: var(--brand-grey);
    font-weight: 600;
    font-size: 28px;
    letter-spacing: 2px;
    text-transform: uppercase;
    white-space: nowrap;
  }
  .card--front .brand {
    left: 50%; top: 50%;
    transform: translate(-50%, -60%);
  }
  .card--back .brand { left: 51px; top: 118px; }

  .holder { position: absolute; left: 51px; top: 340px; }
  .holder__name {
    color: var(--text-grey);
    font-weight: 700;
    font-size: 21px;
    text-transform: uppercase;
    letter-spacing: .2px;
  }
  .holder__role {
    color: var(--accent);
    font-weight: 400;
    font-size: 17px;
    margin-top: 1px;
  }
  .rule {
    position: absolute; left: 51px; top: 402px;
    width: 748px; height: 2px; background: var(--accent);
  }
  .contacts {
    position: absolute; left: 51px; top: 416px; width: 748px;
    display: flex; align-items: center; justify-content: space-between;
    color: var(--text-grey); font-size: 18px; font-weight: 500;
  }
  .contact { display: flex; align-items: center; gap: 12px; }
  .contact svg { width: 18px; height: 18px; flex: none; }
  .contacts__divider { width: 2px; height: 24px; background: var(--accent); }
  .card__band {
    position: absolute; left: 0; bottom: 0;
    width: 100%; height: 12px; background: var(--accent);
  }
</style>
</head>
<body>
  <section class="card card--front" aria-label="Card front">
    <div class="brand">
      <span class="brand__mark"></span>
      <span class="brand__name">Brivo Engineering Tandem</span>
    </div>
  </section>

  <section class="card card--back" aria-label="Card back">
    <div class="brand">
      <span class="brand__mark"></span>
      <span class="brand__name">Brivo Engineering Tandem</span>
    </div>

    <div class="holder">
      <p class="holder__name">Corin B. Hale</p>
      <p class="holder__role">Partner</p>
    </div>

    <div class="rule"></div>

    <div class="contacts">
      <span class="contact">
        <svg viewBox="0 0 18 18" aria-hidden="true"><rect x="3" y="2" width="12" height="14" rx="1.5" fill="none" stroke="#e3bb1f" stroke-width="2"/></svg>
        0123 456 279
      </span>
      <span class="contacts__divider"></span>
      <span class="contact">
        <svg viewBox="0 0 18 18" aria-hidden="true"><rect x="1" y="4" width="16" height="11" fill="#e3bb1f"/><path d="M1 4 L9 10 L17 4 M1 15 L7 9 M17 15 L11 9" fill="none" stroke="#fff" stroke-width="1.2"/></svg>
        info@brivomail.co
      </span>
      <span class="contacts__divider"></span>
      <span class="contact">
        <svg viewBox="0 0 18 18" aria-hidden="true"><circle cx="9" cy="9" r="7.5" fill="none" stroke="#e3bb1f" stroke-width="1.5"/><ellipse cx="9" cy="9" rx="3.2" ry="7.5" fill="none" stroke="#e3bb1f" stroke-width="1.2"/><path d="M1.5 9 H16.5 M3 5 H15 M3 13 H15" stroke="#e3bb1f" stroke-width="1.2"/></svg>
        www.brivoweb.co
      </span>
    </div>

    <div class="card__band"></div>
  </section>
</body>
</html>
```